Wordpress Design for a Private Label BBQ Brand

For our new brand, we'd need a new Wordpress website. We'd prefer to run the website on Wordpress

We'd like to include the following
- space for description of the brand
- space for product portfolio (not a shop!)
- space for socials
- space for support
- space for contact

```html
<!DOCTYPE html>
<html lang="en">
<head>
<meta charset="utf-8">
<title>Fiammaro – BBQ</title>
<link href="https://fonts.googleapis.com/css2?family=Outfit:wght@300;400;500;600;700&display=swap" rel="stylesheet">
<style>
:root{
  --accent:#e0441c;
  --brand-red:#b3121c;
  --ink:#1b1b1b;
  --muted:#4a4a4a;
  --soft:#f4f5f7;
  --cream:#fbf6ef;
  --line:#d8d8d8;
  --white:#ffffff;
}
*{margin:0;padding:0;box-sizing:border-box}
html,body{width:1200px;height:4785px;overflow:hidden;background:var(--white)}
body{position:relative;font-family:"Outfit",sans-serif;color:var(--ink)}
.abs{position:absolute}
.center{left:0;width:1200px;text-align:center}
.btn{position:absolute;background:var(--accent);color:var(--white);border-radius:5px;font-size:15px;display:flex;align-items:center;justify-content:center;gap:10px;font-weight:400}
.h2{font-size:38px;font-weight:600;color:var(--ink)}
.brand-name{font-family:"Outfit",sans-serif;font-weight:600;letter-spacing:1px}
.logo{left:149px;top:58px;font-size:20px;color:var(--ink)}
.logo-dot{left:184px;top:16px;width:34px;height:34px;border-radius:50%;background:var(--accent)}
.nav a{position:absolute;top:41px;font-size:16px;color:var(--ink);text-decoration:none}
.nav a.active{color:var(--accent);font-weight:500}
.hero{left:33px;top:104px;width:1134px;height:481px;background:linear-gradient(160deg,#5d4b3a,#2f2a26 45%,#4a3d33 70%,#1d1b1a);box-shadow:0 14px 22px rgba(0,0,0,.35)}
.hero-welcome{top:252px;font-size:28px;font-weight:300;color:var(--white)}
.hero-title{top:285px;font-size:48px;font-weight:600;color:var(--white);letter-spacing:1px}
.hero-text{top:350px;left:395px;width:410px;text-align:center;font-size:15px;line-height:26px;color:#eee;font-weight:300}
.photo{position:absolute}
.para{font-size:15px;line-height:27px;color:var(--muted);font-weight:300}
.feed{position:absolute;overflow:hidden;box-shadow:0 3px 8px rgba(0,0,0,.15)}
.feed-cap{position:absolute;left:0;right:0;bottom:0;background:linear-gradient(rgba(255,255,255,.55),rgba(255,255,255,.95));padding:0 24px}
.feed-cap b{display:block;font-weight:600;color:var(--ink)}
.feed-cap span{color:var(--muted);font-weight:300}
.forum{left:0;top:1918px;width:1200px;height:587px;background:var(--soft)}
.forum-h{font-size:24px;font-weight:500}
.tab{position:absolute;top:2742px;font-size:19px;color:var(--muted);font-weight:300}
.tab.active{color:var(--ink);font-weight:600}
.tile{position:absolute;background:var(--soft);display:flex;align-items:center;justify-content:center}
.faq{left:149px;width:910px;border-left:5px solid var(--brand-red);display:flex;align-items:center}
.faq.q{background:#f6f6f8}
.faq.a{background:var(--cream)}
.faq .mark{width:80px;padding-left:16px;font-size:30px;font-weight:600;color:var(--brand-red)}
.faq .q-text{font-size:20px;color:var(--ink)}
.faq .a-text{font-size:15px;line-height:27px;color:var(--muted);font-weight:300;width:760px}
.info{left:141px;font-size:14px;color:var(--muted);display:flex;gap:8px;align-items:center}
.footer{left:30px;top:4351px;width:1140px;height:434px;background:var(--brand-red)}
.card{left:492px;top:4147px;width:563px;height:498px;background:var(--white);box-shadow:0 4px 16px rgba(0,0,0,.12)}
.field{position:absolute;left:537px;width:476px;height:37px;border:1.5px solid var(--line);border-radius:19px;background:#fafafa;font-size:14px;color:#999;padding:9px 20px}
.foot-nav a{position:absolute;top:4678px;font-size:16px;color:var(--white);text-decoration:none}
</style>
</head>
<body>
<header>
  <div class="abs logo-dot"></div>
  <div class="abs logo brand-name">FIAMMARO</div>
  <nav class="nav">
    <a class="active" style="left:575px">Home</a>
    <a style="left:682px">About Us</a>
    <a style="left:808px">Portfolio</a>
    <a style="left:930px">FAQ</a>
    <a style="left:1018px">Contact</a>
  </nav>
</header>

<section>
  <div class="abs hero" role="img" aria-label="Blurred photo of people gathered around a grill outdoors"></div>
  <div class="abs center hero-welcome">Welcome to</div>
  <div class="abs center hero-title brand-name">FIAMMARO</div>
  <p class="abs hero-text">Lorem ipsum dolor sit amet, adipiscing elit, sed do eius-mod tempor ut labore et dolore magna aliqua.</p>
  <div class="btn" style="left:535px;top:416px;width:130px;height:41px">Get Started</div>
</section>

<section>
  <div class="photo" style="left:70px;top:635px;width:138px;height:127px;background:linear-gradient(135deg,#6d7178,#c9ccd0)" role="img" aria-label="Meat thermometer probes"></div>
  <div class="photo" style="left:117px;top:799px;width:125px;height:214px;background:radial-gradient(circle at 50% 40%,#3a3a3a,#111)" role="img" aria-label="Black kamado grill"></div>
  <div class="photo" style="left:987px;top:669px;width:174px;height:96px;background:linear-gradient(#2a2a2a,#555)" role="img" aria-label="Tabletop charcoal grill"></div>
  <div class="photo" style="left:1031px;top:858px;width:127px;height:90px;background:linear-gradient(135deg,#d8dadc,#6d7176)" role="img" aria-label="Stainless steel grill tongs"></div>
  <div class="photo" style="left:901px;top:910px;width:69px;height:99px;background:linear-gradient(#9aa0a6,#5d6268)" role="img" aria-label="Grill spatula"></div>
  <div class="abs center h2" style="top:682px">About Us</div>
  <p class="abs para" style="left:305px;top:746px;width:590px;text-align:center">Lorem ipsum dolor sit amet, consectetur adipiscing elit, sed do eiusmod tempor incididunt ut labore et dolore magna aliqua. Quis ipsum suspendisse ultrices gravida. Risus commodo viverra maecenas accumsan lacus vel facilisis. Lorem ipsum dolor sit amet, consectetur adipiscing elit, sed do eiusmod tempor incididunt ut labore et dolore magna aliqua.</p>
  <div class="btn" style="left:535px;top:907px;width:130px;height:41px">Read More</div>
</section>

<section>
  <div class="abs center h2" style="top:1081px">Social Feed</div>
  <div class="feed" style="left:147px;top:1174px;width:611px;height:359px;background:linear-gradient(160deg,#8a9a6a,#4a4a44 50%,#7a5a3a)" role="img" aria-label="Tongs turning skewers and burgers on a grill">
    <div class="feed-cap" style="height:88px;padding-top:8px">
      <b style="font-size:32px">Feed Heading</b><span style="font-size:24px">Lorem Ipsum</span>
      <span style="position:absolute;right:24px;bottom:16px;font-size:22px;color:var(--ink)">15-01-2023</span>
    </div>
  </div>
  <div class="feed" style="left:790px;top:1174px;width:284px;height:216px;background:linear-gradient(160deg,#2b4a7a,#c86a3a 55%,#555)" role="img" aria-label="Plate of vegetable skewers">
    <div class="feed-cap" style="height:68px;padding:8px 16px 0"><b style="font-size:24px">Feed Heading</b><span style="font-size:15px">Lorem Ipsum</span></div>
  </div>
  <div class="feed" style="left:790px;top:1405px;width:284px;height:215px;background:linear-gradient(160deg,#3a2a1a,#d86a1a 50%,#2a2222)" role="img" aria-label="Flames rising from a grill">
    <div class="feed-cap" style="height:78px;padding:12px 16px 0"><b style="font-size:24px">Feed Heading</b><span style="font-size:15px">Lorem Ipsum</span></div>
  </div>
  <div class="feed" style="left:147px;top:1548px;width:295px;height:245px;background:linear-gradient(160deg,#8ab0c8,#5a6a58 60%,#7a6a5a)" role="img" aria-label="Two men grilling outdoors">
    <div class="feed-cap" style="height:72px;padding:12px 22px 0"><b style="font-size:24px">Feed Heading</b><span style="font-size:15px">Lorem Ipsum</span></div>
  </div>
  <div class="feed" style="left:461px;top:1548px;width:297px;height:245px;background:linear-gradient(160deg,#3a2618,#c8561a 55%,#2a1a12)" role="img" aria-label="Food grilling over open flame">
    <div class="feed-cap" style="height:72px;padding:12px 32px 0"><b style="font-size:24px">Feed Heading</b><span style="font-size:15px">Lorem Ipsum</span></div>
  </div>
  <div class="btn" style="left:899px;top:1750px;width:175px;height:43px">View More
    <svg width="30" height="10" viewBox="0 0 30 10"><path d="M0 5H28M23 1l5 4-5 4" stroke="#fff" stroke-width="1.5" fill="none"/></svg>
  </div>
</section>

<section>
  <div class="abs forum"></div>
  <div class="abs center h2" style="top:1964px">Forum</div>
  <div class="photo" style="left:149px;top:2049px;width:176px;height:132px;background:linear-gradient(160deg,#6a5040,#a07a5a 50%,#4a3a30)" role="img" aria-label="Friends sharing a meal at a table"></div>
  <div class="abs forum-h" style="left:360px;top:2054px">Heading 1</div>
  <p class="abs para" style="left:362px;top:2099px;width:490px">Lorem ipsum dolor sit amet, consectetur adipiscing elit, sed do eiusmod tempor incididunt ut labore et dolore magna aliqua. Quis ipsum suspendisse ultrices gravida.</p>
  <div class="btn" style="left:929px;top:2103px;width:132px;height:45px">Read More</div>
  <div class="photo" style="left:149px;top:2218px;width:176px;height:132px;background:linear-gradient(160deg,#8a9a7a,#a0705a 50%,#5a4a3a)" role="img" aria-label="Group of friends at a backyard barbecue"></div>
  <div class="abs forum-h" style="left:358px;top:2223px">Heading 2</div>
  <p class="abs para" style="left:362px;top:2268px;width:490px">Lorem ipsum dolor sit amet, consectetur adipiscing elit, sed do eiusmod tempor incididunt ut labore et dolore magna aliqua. Quis ipsum suspendisse ultrices gravida.</p>
  <div class="btn" style="left:929px;top:2272px;width:132px;height:43px">Read More</div>
  <div class="btn" style="left:535px;top:2413px;width:130px;height:43px">View All</div>
</section>

<section>
  <div class="abs center h2" style="top:2588px">Product Portfolio</div>
  <p class="abs para" style="left:220px;top:2660px;width:760px;text-align:center">Lorem ipsum dolor sit amet, consectetur adipiscing elit, sed do eiusmod tempor incididunt ut labore et dolore magna aliqua. Quis ipsum suspendisse ultrices gravida.</p>
  <div class="tab active" style="left:375px">All</div>
  <div class="tab" style="left:459px">Tongs</div>
  <div class="tab" style="left:567px">Fork</div>
  <div class="tab" style="left:662px">Spatula</div>
  <div class="tab" style="left:785px">BBQ</div>
  <div class="tile" style="left:111px;top:2819px;width:324px;height:249px"><div role="img" aria-label="Kamado grill" style="width:110px;height:200px;background:radial-gradient(circle at 50% 35%,#444,#111)"></div></div>
  <div class="tile" style="left:446px;top:2819px;width:321px;height:249px"><div role="img" aria-label="Tongs, fork and spatula set" style="width:140px;height:160px;background:linear-gradient(90deg,#9aa0a6,#2a2a2a,#9aa0a6)"></div></div>
  <div class="tile" style="left:778px;top:2819px;width:324px;height:249px"><div role="img" aria-label="Grill tool set in case" style="width:130px;height:120px;background:linear-gradient(#4a4e54,#1a1c1f)"></div></div>
  <div class="tile" style="left:111px;top:3077px;width:324px;height:249px"><div role="img" aria-label="Tabletop charcoal grill" style="width:170px;height:90px;background:linear-gradient(#2a2a2a,#555)"></div></div>
  <div class="tile" style="left:446px;top:3077px;width:321px;height:249px"><div role="img" aria-label="Closed aluminium tool case" style="width:170px;height:80px;background:linear-gradient(#c4c8cc,#7a7f84)"></div></div>
  <div class="tile" style="left:778px;top:3077px;width:324px;height:249px"><div role="img" aria-label="Meat thermometer probes" style="width:100px;height:120px;background:linear-gradient(90deg,#3a3c40,#b0b4b8,#3a3c40)"></div></div>
  <div class="btn" style="left:535px;top:3368px;width:130px;height:45px">View All</div>
</section>

<section>
  <div class="abs center h2" style="top:3482px">FAQs</div>
  <div class="abs center" style="top:3540px;font-size:21px">Commonly asked questions.</div>
  <div class="abs faq q" style="top:3604px;height:75px"><span class="mark">Q.</span><span class="q-text">What is a quality of BBQ Products?</span></div>
  <div class="abs faq a" style="top:3679px;height:121px"><span class="mark">A.</span><span class="a-text">Lorem ipsum dolor sit amet, consectetur adipiscing elit, sed do eiusmod tempor incididunt ut labore et dolore magna aliqua. Quis ipsum suspendisse ultrices gravida. Risus commodo viverra maecenas accumsan lacus vel facilisis.</span></div>
  <div class="abs faq q" style="top:3800px;height:80px"><span class="mark">Q.</span><span class="q-text">What is a quality of BBQ Products?</span></div>
  <div class="abs faq a" style="top:3880px;height:119px"><span class="mark">A.</span><span class="a-text">Lorem ipsum dolor sit amet, consectetur adipiscing elit, sed do eiusmod tempor incididunt ut labore et dolore magna aliqua. Quis ipsum suspendisse ultrices gravida. Risus commodo viverra maecenas accumsan lacus vel facilisis.</span></div>
  <div class="btn" style="left:535px;top:4037px;width:130px;height:45px">View More</div>
</section>

<footer>
  <div class="abs footer"></div>
  <div class="abs h2" style="left:141px;top:4150px">Contact us Today</div>
  <div class="abs info" style="top:4236px"><svg width="10" height="13" viewBox="0 0 10 13"><path d="M5 0a5 5 0 0 0-5 5c0 3.5 5 8 5 8s5-4.5 5-8a5 5 0 0 0-5-5zm0 7a2 2 0 1 1 0-4 2 2 0 0 1 0 4z" fill="#222"/></svg>#7, Ember Lane, USA 40512</div>
  <div class="abs info" style="top:4262px"><svg width="11" height="11" viewBox="0 0 11 11"><path d="M2 0l2 3-1 1.5c.8 1.5 2 2.7 3.5 3.5L8 7l3 2-1 2C5 11 0 6 0 1z" fill="#222"/></svg>+1 555 014 2290</div>
  <div class="abs info" style="top:4288px"><svg width="12" height="9" viewBox="0 0 12 9"><rect x=".5" y=".5" width="11" height="8" fill="none" stroke="#222"/><path d="M.5.5 6 5l5.5-4.5" fill="none" stroke="#222"/></svg>info@fiammaro.com</div>

  <div class="abs card"></div>
  <div class="field" style="top:4180px">First Name</div>
  <div class="field" style="top:4246px">Last Name</div>
  <div class="field" style="top:4311px">Phone Number</div>
  <div class="field" style="top:4374px">Email</div>
  <div class="field" style="top:4439px;height:122px;border-radius:14px">Message</div>
  <div class="btn" style="left:539px;top:4587px;width:132px;height:43px">Submit</div>

  <div class="abs" style="left:180px;top:4392px;width:40px;height:40px;border-radius:50%;background:var(--white)"></div>
  <div class="abs brand-name" style="left:149px;top:4452px;font-size:24px;color:var(--white)">FIAMMARO</div>
  <p class="abs" style="left:149px;top:4520px;width:290px;font-size:15px;line-height:27px;color:var(--white);font-weight:300">Lorem ipsum dolor sit amet, consecte-tur adipiscing elit, sed do eiusmod tempor ut let dolore magna aliqua.</p>
  <nav class="foot-nav">
    <a style="left:349px">Home</a>
    <a style="left:454px">About Us</a>
    <a style="left:581px">Portfolio</a>
    <a style="left:703px">FAQ</a>
    <a style="left:790px">Contact</a>
  </nav>
  <div class="abs" style="left:30px;top:4719px;width:1140px;height:1px;background:rgba(255,255,255,.45)"></div>
  <div class="abs" style="left:149px;top:4745px;font-size:11px;color:var(--white);font-weight:300">© copyrights 2023 Fiammaro | All Rights Reserved</div>
</footer>
</body>
</html>
```